Mobile Fitness snd Therapy Business Card Design

I need a business card designed for my mobile fitness and therapy business.

Please view the images that I have uploaded. I like the simplicity of the design that I have attached. I adapted it with my information

Target Market(s)

Those seeking personal training, injury rehabilitation or massage therapy.

Industry/Entity Type

Business

Contact Information for Business Card

Derek Fulham - MSc, CAT(C), RMT, CSCS, Pn2
e-mail: derek@vantrelo.com
website: www.vantrelo.com
instagram: @derek_fulham

Font styles to use
Sans Serif

Colors
3176b5
0355a3

Requirements
Must have
• "Contact us to receive a FREE assessment"
• Services offered:
• Personal Training
• Golf Fitness
• Injury Rehab
• Massage Therapy
• Yoga
Nice to have
• Consistent colours with brand
• - Dark Blue: #232837
• - Blue: #5096f0
• Consistent look/feel with the website: www.vantrelo.com

```html
<!DOCTYPE html>
<html lang="en">
<head>
<meta charset="utf-8">
<title>Vantrelo Business Card</title>
<link rel="stylesheet" href="https://fonts.googleapis.com/css2?family=Open+Sans:wght@400;600;700;800&display=swap">
<style>
  :root {
    --navy: #232837;
    --sky: #8cbef8;
    --paper: #f6f7f9;
    --white: #ffffff;
    --stage: #e4e6ea;
  }
  * { box-sizing: border-box; margin: 0; padding: 0; }
  html, body {
    width: 1200px;
    height: 900px;
    overflow: hidden;
    background: var(--stage);
    font-family: "Open Sans", Arial, sans-serif;
  }
  .business-card {
    position: absolute;
    left: 111px;
    top: 147px;
    width: 978px;
    height: 606px;
    display: grid;
    grid-template-rows: 171px 224px 60px 151px;
    box-shadow: 0 12px 30px rgba(0,0,0,0.18);
    overflow: hidden;
  }
  .card-header {
    background: var(--navy);
    color: var(--white);
    display: flex;
    justify-content: space-between;
    padding: 34px 42px 0 42px;
  }
  .identity { padding-top: 40px; }
  .identity-name {
    font-weight: 700;
    font-size: 35px;
    letter-spacing: 0.5px;
    line-height: 1.1;
  }
  .identity-credentials {
    font-size: 23px;
    margin-top: 6px;
    opacity: 0.95;
  }
  .contact-list {
    list-style: none;
    text-align: right;
    font-size: 27px;
    line-height: 1.38;
  }
  .contact-label { font-weight: 700; }
  .brand-panel {
    background: var(--paper);
    display: flex;
    flex-direction: column;
    align-items: center;
    justify-content: center;
    padding-top: 6px;
  }
  .brand-name {
    color: var(--navy);
    font-weight: 800;
    font-size: 96px;
    letter-spacing: 12px;
    padding-left: 12px;
    line-height: 1;
  }
  .brand-tagline {
    color: var(--navy);
    font-weight: 700;
    font-size: 30px;
    letter-spacing: 5.5px;
    padding-left: 5.5px;
    margin-top: 14px;
  }
  .offer-band {
    background: var(--sky);
    color: var(--white);
    font-weight: 700;
    font-size: 30px;
    display: flex;
    align-items: center;
    justify-content: center;
  }
  .services {
    background: var(--navy);
    color: var(--white);
    font-weight: 600;
    font-size: 38px;
    text-align: center;
    line-height: 1.4;
    padding-top: 24px;
  }
</style>
</head>
<body>
  <article class="business-card">
    <header class="card-header">
      <div class="identity">
        <h1 class="identity-name">DEREK FULHAM</h1>
        <p class="identity-credentials">MSc, CAT(C), RMT, CSCS, Pn2</p>
      </div>
      <ul class="contact-list">
        <li><span class="contact-label">E:</span> derek@vantrelo.com</li>
        <li><span class="contact-label">W:</span> www.vantrelo.com</li>
        <li><span class="contact-label">I:</span> @derek_fulham</li>
      </ul>
    </header>
    <section class="brand-panel">
      <p class="brand-name">VANTRELO</p>
      <p class="brand-tagline">NUTRITION - FITNESS - HEALTH</p>
    </section>
    <p class="offer-band">Contact us to receive a FREE assessment</p>
    <section class="services">
      <p>Personal Training | Golf Fitness</p>
      <p>Injury Rehab | Massage Therapy | Yoga</p>
    </section>
  </article>
</body>
</html>
```